Business Management Fortress

Assist with enhancing a powerpoint slide by providing a few design options for consideration. I have a template but open to any creative ideas.

Internal employees and stakeholders

Business Management, Finance, Accounting

• Maintain a fortress, temple, or pyramid schema
• Scenic Background

```html
<!DOCTYPE html>
<html lang="en">
<head>
<meta charset="utf-8">
<title>Business Management Fortress</title>
<link href="https://fonts.googleapis.com/css2?family=Oswald:wght@300;400;500&display=swap" rel="stylesheet">
<style>
  :root {
    --sky-top: #1f4f9c;
    --sky-mid: #5f8cc4;
    --haze: #d9c7a6;
    --sand: #c8a26a;
    --sand-deep: #a57c45;
    --tier-light: #1ecbd8;
    --tier-dark: #13b0c0;
    --tier-edge: #0e97a6;
    --gold-light: #ffd62a;
    --gold-dark: #f2b100;
    --label: #ffffff;
    --heading: #1f1f1f;
  }
  html, body {
    margin: 0;
    padding: 0;
    overflow: hidden;
  }
  .slide {
    position: relative;
    width: 1200px;
    height: 678px;
    overflow: hidden;
    font-family: "Oswald", "Arial Narrow", sans-serif;
  }
  .scenic-backdrop {
    position: absolute;
    inset: 0;
    background:
      linear-gradient(180deg, var(--sky-top) 0%, var(--sky-mid) 38%, #a9bdd0 62%, var(--haze) 76%, var(--sand) 88%, var(--sand-deep) 100%);
  }
  .pyramid {
    position: absolute;
    inset: 0;
  }
  .tier-label {
    fill: var(--label);
    font-family: "Oswald", "Arial Narrow", sans-serif;
    font-weight: 500;
    font-size: 11.5px;
    text-anchor: middle;
  }
  .leader-label {
    fill: #1a1a1a;
    font-family: "Oswald", "Arial Narrow", sans-serif;
    font-weight: 400;
    font-size: 11px;
    text-anchor: middle;
  }
  .section-heading {
    fill: var(--heading);
    font-family: "Oswald", "Arial Narrow", sans-serif;
    font-weight: 400;
    font-size: 19px;
    text-anchor: middle;
  }
  .icon {
    fill: none;
    stroke: var(--label);
    stroke-width: 1.6;
    stroke-linecap: round;
    stroke-linejoin: round;
  }
  .icon-dark {
    fill: none;
    stroke: #1a1a1a;
    stroke-width: 1.2;
  }
</style>
</head>
<body>
<div class="slide">
  <div class="scenic-backdrop" role="img" aria-label="Photograph of the pyramids of Giza under a blue sky with wispy clouds, desert sand and a distant city skyline"></div>

  <svg class="pyramid" width="1200" height="678" viewBox="0 0 1200 678" xmlns="http://www.w3.org/2000/svg">
    <defs>
      <linearGradient id="gold" x1="0" x2="1" y1="0" y2="0">
        <stop offset="0" stop-color="var(--gold-light)"/>
        <stop offset="1" stop-color="var(--gold-dark)"/>
      </linearGradient>
    </defs>

    <!-- Leader apex -->
    <polygon points="585,44 631,123 539,123" fill="url(#gold)"/>
    <rect x="539" y="123" width="92" height="3" fill="var(--tier-edge)"/>
    <g class="icon-dark">
      <circle cx="576" cy="76" r="2.5"/><circle cx="585" cy="74" r="2.5"/><circle cx="594" cy="76" r="2.5"/>
      <path d="M571 90 v-6 a5 5 0 0 1 10 0 v6 M580 90 v-7 a5 5 0 0 1 10 0 v7 M589 90 v-6 a5 5 0 0 1 10 0 v6"/>
    </g>
    <text class="leader-label" x="585" y="108">LEADER</text>

    <!-- Tier: Partner / Profitability -->
    <polygon points="514,132 585,132 585,217 486,217" fill="var(--tier-light)"/>
    <polygon points="585,132 656,132 683,217 585,217" fill="var(--tier-dark)"/>
    <polygon points="486,214 683,214 683,218 486,218" fill="var(--tier-edge)"/>
    <g class="icon" transform="translate(552,163)">
      <path d="M-13 -6 l6 -3 l6 4 l6 -4 l6 3 M-10 -4 l7 8 a2 2 0 0 0 3 0 l6 -7"/>
      <path d="M-5 1 l3 3 M-2 -1 l3 3"/>
    </g>
    <g class="icon" transform="translate(623,163)">
      <path d="M-8 -10 h16 l-6 8 v4 h-4 v-4 z"/>
      <circle cx="0" cy="8" r="4"/>
      <circle cx="-2" cy="-13" r="1"/><circle cx="3" cy="-14" r="1"/>
    </g>
    <text class="tier-label" x="548" y="198">PARTNER</text>
    <text class="tier-label" x="626" y="198">PROFITABILITY</text>

    <!-- Tier: People / Innovation -->
    <polygon points="476,224 585,224 585,309 434,309" fill="var(--tier-light)"/>
    <polygon points="585,224 694,224 736,309 585,309" fill="var(--tier-dark)"/>
    <polygon points="434,306 736,306 736,310 434,310" fill="var(--tier-edge)"/>
    <g class="icon" transform="translate(523,254)">
      <circle cx="-6" cy="-6" r="3.5"/><circle cx="6" cy="-6" r="3.5"/><circle cx="0" cy="-1" r="4"/>
      <path d="M-9 11 a9 8 0 0 1 18 0 M-14 3 a7 6 0 0 1 7 -4 M14 3 a7 6 0 0 0 -7 -4"/>
    </g>
    <g class="icon" transform="translate(649,253)">
      <path d="M-4 7 v-3 a8 8 0 1 1 8 0 v3 z M-3 10 h6"/>
      <path d="M0 4 v-6"/>
    </g>
    <text class="tier-label" x="521" y="288">PEOPLE</text>
    <text class="tier-label" x="649" y="287">INNOVATION</text>

    <!-- Tier: Business Intelligence / Strategic Alliances -->
    <polygon points="425,314 585,314 585,400 381,400" fill="var(--tier-light)"/>
    <polygon points="585,314 747,314 789,400 585,400" fill="var(--tier-dark)"/>
    <polygon points="381,396 789,396 789,401 381,401" fill="var(--tier-edge)"/>
    <g class="icon" transform="translate(491,346)">
      <circle r="11" stroke-dasharray="4 2.5"/>
      <circle r="6"/>
      <path d="M-6 0 h12 M0 -6 v12"/>
    </g>
    <g class="icon" transform="translate(678,346)">
      <rect x="-11" y="-13" width="22" height="27" rx="1.5"/>
      <rect x="-4" y="-15" width="8" height="4"/>
      <path d="M-6 4 l4 -5 l4 3 l5 -7 M-6 9 h12"/>
    </g>
    <text class="tier-label" x="491" y="381">BUSINESS INTELLIGENCE</text>
    <text class="tier-label" x="678" y="384">STRATEGIC ALLIANCES</text>

    <!-- Section heading -->
    <text class="section-heading" x="579" y="422">FIDUCIARY RESPONSIBILITIES</text>

    <!-- Tier: Accurate Financials / Internal Controls / Brand Protection -->
    <polygon points="375,430 585,430 585,516 328,516" fill="var(--tier-light)"/>
    <polygon points="585,430 797,430 841,516 585,516" fill="var(--tier-dark)"/>
    <polygon points="328,512 841,512 841,517 328,517" fill="var(--tier-edge)"/>
    <g class="icon" transform="translate(435,461)">
      <rect x="-11" y="-12" width="14" height="24" rx="1"/>
      <rect x="1" y="-5" width="10" height="15" rx="1"/>
      <path d="M-7 8 v-4 M-4 8 v-7 M-1 8 v-5 M4 -1 h4 M4 3 h4"/>
    </g>
    <g class="icon" transform="translate(586,461)">
      <path d="M-13 -8 h26 M-13 0 h26 M-13 8 h26"/>
      <circle cx="6" cy="-8" r="2.2"/><circle cx="-6" cy="0" r="2.2"/><circle cx="3" cy="8" r="2.2"/>
    </g>
    <g class="icon" transform="translate(729,461)">
      <path d="M0 -10 l10 3 v6 c0 7 -5 11 -10 13 c-5 -2 -10 -6 -10 -13 v-6 z"/>
      <path d="M-4 1 l3 3 l6 -6"/>
      <path d="M-12 -12 l-2 -2 M12 -12 l2 -2 M0 -14 v-2"/>
    </g>
    <text class="tier-label" x="435" y="496">ACCURATE FINANCIALS</text>
    <text class="tier-label" x="586" y="496">INTERNAL CONTROLS</text>
    <text class="tier-label" x="734" y="496">BRAND PROTECTION</text>

    <!-- Tier: Compliance / Ethics / Cost Management -->
    <polygon points="322,522 584,522 584,607 266,607" fill="var(--tier-light)"/>
    <polygon points="584,522 850,522 904,607 584,607" fill="var(--tier-dark)"/>
    <polygon points="266,603 904,603 904,608 266,608" fill="var(--tier-edge)"/>
    <g class="icon" transform="translate(390,554)">
      <path d="M-10 -12 h16 v22 a3 3 0 0 1 -3 3 h-13 a3 3 0 0 0 3 -3 v-20 a2 2 0 0 0 -3 0"/>
      <path d="M1 -5 l4 1.5 v3 c0 3 -2 5 -4 6 c-2 -1 -4 -3 -4 -6 v-3 z"/>
    </g>
    <g class="icon" transform="translate(586,552)">
      <circle cx="-2" cy="-9" r="4.5" fill="var(--label)"/>
      <path d="M-12 12 v-3 a9 8 0 0 1 14 -7"/>
      <path d="M8 -2 l6 2 v5 c0 5 -3 7 -6 8 c-3 -1 -6 -3 -6 -8 v-5 z"/>
    </g>
    <g class="icon" transform="translate(777,553)">
      <circle cx="0" cy="-9" r="7"/>
      <path d="M2 -12 h-3 a1.5 1.5 0 0 0 0 3 h2 a1.5 1.5 0 0 1 0 3 h-3 M0 -14 v1.5 M0 -6 v1.5"/>
      <path d="M-13 6 h6 l6 2 h6 l6 -4 M-13 11 h7 l6 2 l12 -6"/>
    </g>
    <text class="tier-label" x="390" y="589">COMPLIANCE</text>
    <text class="tier-label" x="586" y="587">ETHICS</text>
    <text class="tier-label" x="774" y="588">COST MANAGEMENT</text>
  </svg>
</div>
</body>
</html>
```